Business cards to launch an education platform

Hi,
I am looking at having new business cards designed.
I am a startup, developing a web platform for schools and university, the education world. It's an online assessment system.
I would like a card that looks classy, and that is using the colors and the font of my logo.

I have attached:
1) my logo
2) A business card that I have designed quickly so you can have all the information required in the card, but I really don't like it.
3) The font that I am using (Lato Regular) to design my web platform
4) Some screenshots of my web platform so you can have a look at the style that I have.

Target Market(s)

Major market: Education system: Schools and university
Minor markets: Business in general

Industry/Entity Type

Business

Contact Information for Business Card

Clara Fenwick
Director

M: 0437 518 902
E: clara.fenwick@amberLoomSystems.com.au

Requirements
Must have
• The colors of my logo

```html
<!DOCTYPE html>
<html lang="en">
<head>
<meta charset="utf-8">
<title>Amber Loom Systems — Business Cards</title>
<link rel="stylesheet" href="https://fonts.googleapis.com/css2?family=Lato:wght@400&family=Roboto+Condensed:wght@400;500&display=swap">
<style>
  :root {
    --page-bg: #a3a4a6;
    --card-white: #eeeef0;
    --navy: #063563;
    --brand-blue: #1f6fb5;
    --name-navy: #17365f;
    --text-grey: #4a4f57;
    --back-text: #e6e7ec;
    --shadow: rgba(0, 0, 0, 0.28);
  }
  * { margin: 0; padding: 0; box-sizing: border-box; }
  html, body {
    width: 1105px;
    height: 1200px;
    overflow: hidden;
    background: var(--page-bg);
  }
  .sheet {
    position: relative;
    width: 1105px;
    height: 1200px;
  }
  .card {
    position: absolute;
    left: 122px;
    width: 860px;
    height: 491px;
    box-shadow: 0 10px 22px var(--shadow);
  }
  .card-front { top: 95px; background: var(--card-white); }
  .card-back { top: 628px; background: var(--navy); }

  /* front: brand block */
  .brand {
    position: absolute;
    left: 80px;
    top: 140px;
    width: 280px;
    text-align: center;
    font-family: "Lato", sans-serif;
    font-weight: 400;
    color: var(--brand-blue);
  }
  .brand-mark {
    display: block;
    width: 70px;
    height: 70px;
    margin: 0 auto 26px;
    background: var(--brand-blue);
  }
  .brand-name {
    font-size: 34px;
    line-height: 1.15;
    letter-spacing: 1.5px;
  }

  /* front: contact block */
  .contact {
    position: absolute;
    left: 402px;
    top: 142px;
    font-family: "Roboto Condensed", sans-serif;
  }
  .person-name {
    font-size: 40px;
    font-weight: 500;
    color: var(--name-navy);
    line-height: 1.1;
  }
  .person-role {
    font-size: 30px;
    font-weight: 400;
    color: var(--text-grey);
    margin-top: 4px;
  }
  .details {
    list-style: none;
    margin-top: 30px;
  }
  .details li {
    display: flex;
    align-items: center;
    gap: 16px;
    font-size: 20px;
    color: var(--text-grey);
    height: 34px;
  }
  .details svg { width: 18px; height: 18px; fill: var(--name-navy); flex: none; }

  /* back */
  .back-name {
    position: absolute;
    left: 0;
    right: 0;
    top: 190px;
    text-align: center;
    font-family: "Lato", sans-serif;
    font-weight: 400;
    font-size: 52px;
    letter-spacing: 2px;
    color: var(--back-text);
  }
  .back-web {
    position: absolute;
    left: 0;
    right: 0;
    top: 410px;
    text-align: center;
    font-family: "Lato", sans-serif;
    font-size: 25px;
    letter-spacing: 0.5px;
    color: var(--back-text);
  }
</style>
</head>
<body>
<main class="sheet">
  <section class="card card-front" aria-label="Card front">
    <div class="brand">
      <span class="brand-mark"></span>
      <p class="brand-name">Amber Loom<br>Systems</p>
    </div>
    <div class="contact">
      <h1 class="person-name">Clara Fenwick</h1>
      <p class="person-role">Director</p>
      <ul class="details">
        <li>
          <svg viewBox="0 0 18 18" aria-hidden="true"><path d="M5 0h8a2 2 0 0 1 2 2v14a2 2 0 0 1-2 2H5a2 2 0 0 1-2-2V2a2 2 0 0 1 2-2zm0 2v11h8V2zm4 12.2a1 1 0 1 0 0 2 1 1 0 0 0 0-2z"/></svg>
          0437 518 902
        </li>
        <li>
          <svg viewBox="0 0 18 18" aria-hidden="true"><path d="M1 4h16v1.2L9 10 1 5.2zm0 2.6 8 4.8 8-4.8V14H1z"/></svg>
          clara.fenwick@amberLoomSystems.com.au
        </li>
        <li>
          <svg viewBox="0 0 18 18" aria-hidden="true"><circle cx="9" cy="9" r="8"/><path d="M5 5c2 0 3 1 2.5 2.5S5 9 6 11s2 2 1.5 4M11 3c0 2 2 2 3 3.5s0 3-1.5 3.5" stroke="#eeeef0" stroke-width="1.3" fill="none"/></svg>
          www.amberLoomSystems.com.au
        </li>
      </ul>
    </div>
  </section>

  <section class="card card-back" aria-label="Card back">
    <p class="back-name">Amber Loom Systems</p>
    <p class="back-web">www.amberLoomSystems.com.au</p>
  </section>
</main>
</body>
</html>
```